Web Meeting Company Needs Bullet Point Icons for Power Point Presentation

I need 6 Icons / Buttons built to place into a power point presentation.

I have attached 2 slides. The first slide has the exsisting icons that we are using. On the next slide we need Icons that look similar to those in slide one, but reflect the discriptions that are listed next to the current Icons.

- Crowd Sourcing
- Kick Starters
- Segmentation
- Build A...
- Pop-Ups
- Gamification

On Slide 2 I have also uploaded a screen shot of some icons from BrindleVault that i think would work from a symbol standpoint

Target Market(s)

Pharma Meeting Planning

Industry/Entity Type

It Company

Requirements
Must have
• Icons
Nice to have
• Icons
Should not have
• Icons

```html
<!DOCTYPE html>
<html lang="en">
<head>
<meta charset="utf-8">
<title>Audience Engagement Themes</title>
<link href="https://fonts.googleapis.com/css2?family=Arimo:ital,wght@0,400;0,700;1,400&display=swap" rel="stylesheet">
<style>
  :root {
    --bg: #ffffff;
    --frame: #d4d4d4;
    --title: #b4409e;
    --label: #f7931e;
    --band: #48c3d3;
    --footer-text: #6f6f6f;
    --brand: #7d7d7d;
    --icon-line: #ffffff;
  }
  * { margin: 0; padding: 0; box-sizing: border-box; }
  html, body { width: 1200px; height: 888px; overflow: hidden; background: var(--bg); }
  .slide {
    position: relative; width: 1200px; height: 888px;
    border: 1px solid var(--frame); background: var(--bg);
    font-family: "Arimo", Arial, sans-serif; overflow: hidden;
  }
  .slide-title {
    position: absolute; left: 72px; top: 70px;
    font-size: 43px; font-weight: 400; color: var(--title); letter-spacing: 0.3px;
  }
  .theme-list { list-style: none; }
  .theme {
    position: absolute; left: 57px; display: flex; align-items: center; height: 94px;
  }
  .theme-icon { width: 94px; height: 94px; flex: none; }
  .theme-label {
    margin-left: 6px; font-size: 28px; font-weight: 700; color: var(--label);
    text-shadow: 1px 1px 1px rgba(0,0,0,0.18);
  }
  .brand {
    position: absolute; left: 925px; top: 758px; display: flex; align-items: center; gap: 10px;
  }
  .brand-name { font-size: 50px; font-weight: 400; color: var(--brand); letter-spacing: -1px; }
  .brand-mark { width: 30px; height: 30px; background: var(--brand); border-radius: 50%; }
  .footer-band {
    position: absolute; left: 0; bottom: 0; width: 100%; height: 47px; background: var(--band);
  }
  .footer-notch {
    position: absolute; left: 128px; top: 0;
    border-left: 12px solid transparent; border-right: 12px solid transparent;
    border-top: 10px solid var(--bg);
  }
  .slide-number {
    position: absolute; right: 52px; top: 16px;
    font-size: 16px; font-style: italic; color: var(--footer-text);
  }
</style>
</head>
<body>
<div class="slide">
  <h1 class="slide-title">Audience Engagement Themes</h1>

  <svg width="0" height="0" style="position:absolute">
    <defs>
      <linearGradient id="g-green" x1="0" y1="0" x2="0" y2="1"><stop offset="0" stop-color="#86dc4f"/><stop offset="1" stop-color="#47a51a"/></linearGradient>
      <linearGradient id="g-orange" x1="0" y1="0" x2="0" y2="1"><stop offset="0" stop-color="#ff9445"/><stop offset="1" stop-color="#ee5d08"/></linearGradient>
      <linearGradient id="g-blue" x1="0" y1="0" x2="0" y2="1"><stop offset="0" stop-color="#82abd8"/><stop offset="1" stop-color="#2b4f8c"/></linearGradient>
      <linearGradient id="g-olive" x1="0" y1="0" x2="0" y2="1"><stop offset="0" stop-color="#a1c871"/><stop offset="1" stop-color="#6c9b3c"/></linearGradient>
      <linearGradient id="g-tan" x1="0" y1="0" x2="0" y2="1"><stop offset="0" stop-color="#f6b97f"/><stop offset="1" stop-color="#cf8646"/></linearGradient>
      <linearGradient id="g-purple" x1="0" y1="0" x2="0" y2="1"><stop offset="0" stop-color="#d495c3"/><stop offset="1" stop-color="#954383"/></linearGradient>
    </defs>
  </svg>

  <ul class="theme-list">
    <li class="theme" style="top:155px">
      <svg class="theme-icon" viewBox="0 0 100 100" aria-hidden="true">
        <circle cx="50" cy="50" r="49" fill="url(#g-green)"/>
        <g fill="none" stroke="var(--icon-line)" stroke-width="2.5" stroke-linecap="round">
          <circle cx="50" cy="30" r="8"/><path d="M47 40h6M50 14v4M36 20l3 3M64 20l-3 3M32 31h4M64 31h4"/>
        </g>
        <g fill="var(--icon-line)">
          <circle cx="34" cy="55" r="4.5"/><circle cx="66" cy="55" r="4.5"/><circle cx="50" cy="57" r="5"/>
          <path d="M26 72q0-10 8-10t8 10zM58 72q0-10 8-10t8 10z"/><path d="M40 78q0-13 10-13t10 13z"/>
        </g>
      </svg>
      <span class="theme-label">Crowd Sourcing</span>
    </li>
    <li class="theme" style="top:264px">
      <svg class="theme-icon" viewBox="0 0 100 100" aria-hidden="true">
        <circle cx="50" cy="50" r="49" fill="url(#g-orange)"/>
        <g fill="var(--icon-line)">
          <path d="M72 22q-20 2-30 24l12 12q22-10 24-30z"/>
          <path d="M40 46l-12 2-6 8 12 0zM54 60l-2 12-8 6 0-12z"/>
          <path d="M36 62l-8 14 4-2 4 4 2-6 6-2z"/>
        </g>
        <circle cx="62" cy="36" r="4" fill="url(#g-orange)"/>
      </svg>
      <span class="theme-label">Kick Starters</span>
    </li>
    <li class="theme" style="top:377px">
      <svg class="theme-icon" viewBox="0 0 100 100" aria-hidden="true">
        <circle cx="50" cy="50" r="49" fill="url(#g-blue)"/>
        <g fill="none" stroke="var(--icon-line)" stroke-width="3.5">
          <circle cx="50" cy="50" r="30"/>
          <path d="M50 20v60M24 35l52 30M24 65l52-30"/>
        </g>
      </svg>
      <span class="theme-label">Segmentation</span>
    </li>
    <li class="theme" style="top:498px">
      <svg class="theme-icon" viewBox="0 0 100 100" aria-hidden="true">
        <circle cx="50" cy="50" r="49" fill="url(#g-olive)"/>
        <path fill="var(--icon-line)" d="M6 30h70q18 0 22 26q-8-12-22-12h-20v54h-14v-54h-36z"/>
      </svg>
      <span class="theme-label" style="margin-left:16px">Build a…</span>
    </li>
    <li class="theme" style="top:610px">
      <svg class="theme-icon" viewBox="0 0 100 100" aria-hidden="true">
        <circle cx="50" cy="50" r="49" fill="url(#g-tan)"/>
        <g fill="none" stroke="var(--icon-line)" stroke-width="5" stroke-linejoin="round">
          <path d="M46 36h-16v30h34v-10"/>
          <path d="M40 58q2-18 22-18"/>
        </g>
        <path fill="var(--icon-line)" d="M60 30l14 10-14 10z"/>
      </svg>
      <span class="theme-label" style="margin-left:12px">Pop Ups</span>
    </li>
    <li class="theme" style="top:721px">
      <svg class="theme-icon" viewBox="0 0 100 100" aria-hidden="true">
        <circle cx="50" cy="50" r="49" fill="url(#g-purple)"/>
        <path fill="var(--icon-line)" d="M30 38h40q12 0 12 18t-8 16q-6 0-10-8h-28q-4 8-10 8t-8-16 12-18z"/>
        <path d="M50 30v8" stroke="var(--icon-line)" stroke-width="2.5"/>
        <g fill="url(#g-purple)">
          <path d="M32 47h4v5h5v4h-5v5h-4v-5h-5v-4h5z"/>
          <circle cx="64" cy="48" r="2.6"/><circle cx="64" cy="58" r="2.6"/><circle cx="59" cy="53" r="2.6"/><circle cx="69" cy="53" r="2.6"/>
        </g>
      </svg>
      <span class="theme-label" style="margin-left:0">Gamification</span>
    </li>
  </ul>

  <div class="brand">
    <span class="brand-name">Tessera</span>
    <span class="brand-mark"></span>
  </div>

  <footer class="footer-band">
    <span class="footer-notch"></span>
    <span class="slide-number">slide 2</span>
  </footer>
</div>
</body>
</html>
```